UX - Need some screens design for a Skill Assessment Application

I am building an app to carry out skill assessments. Depending on how the assessment is configured, it may have one or more parts
1. Question based assessment (Multiple Choice, True False, Fill in the blanks"
2. Endorsement by two colleagues - A screen that allows user to pick colleagues based on search and shows the status of pending requests
3. A written submission - a page that explains the format of the submission and a file upload
As each assessment can be configured with or without any of the steps, the assessment UI must be such that these areas get hidden/displayed based on configuration.
Colour codes to be used can be #0e78bb and #ffffff
There will also be a start screen (instructions) and an end screen (results)
Target Market(s)
Enterprise software
Number of Pages Required
4 page

```html
<!DOCTYPE html>
<html lang="en">
<head>
<meta charset="utf-8">
<title>Upload Documents</title>
<link href="https://fonts.googleapis.com/css2?family=Inter:wght@400;500;600;700&display=swap" rel="stylesheet">
<style>
  :root {
    --brand: #0e56a9;
    --accent: #0e78bb;
    --white: #ffffff;
    --page: #f5f6f8;
    --ink: #2b2b2b;
    --muted: #555b61;
    --label: #4a4f55;
    --placeholder: #9a9fa5;
    --line: #d7dadd;
    --dash: #cfd2d5;
    --drop: #f8f8f9;
    --icon-bg: #e6e7e9;
    --icon: #8e9398;
    --nav-dim: #c9d8ee;
  }
  * { box-sizing: border-box; margin: 0; padding: 0; }
  html, body { width: 1200px; height: 686px; overflow: hidden; }
  body {
    position: relative;
    font-family: "Inter", Arial, sans-serif;
    background: var(--page);
    color: var(--ink);
  }
  .topbar {
    position: absolute; left: 0; top: 0; width: 1200px; height: 43px;
    background: var(--brand); color: var(--white);
  }
  .brand {
    position: absolute; left: 57px; top: 12px;
    display: flex; align-items: center; gap: 8px;
    font-size: 15px; font-weight: 600;
  }
  .brand-dot { width: 18px; height: 18px; border-radius: 50%; background: var(--white); }
  .nav { position: absolute; top: 15px; font-size: 12.5px; color: var(--nav-dim); }
  .nav.active { color: var(--white); font-weight: 700; }
  .avatar {
    position: absolute; left: 1101px; top: 8px; width: 27px; height: 27px;
    border-radius: 50%; background: linear-gradient(135deg, #c7d3e4, #5f6d84);
  }
  .avatar-caret { position: absolute; left: 1133px; top: 16px; }

  .page-head {
    position: absolute; left: 0; top: 43px; width: 1200px; height: 97px;
    background: var(--white); border-bottom: 1px solid var(--line);
  }
  .back { position: absolute; left: 57px; top: 22px; }
  .crumbs { position: absolute; left: 88px; top: 25px; font-size: 11px; color: var(--muted); }
  .crumbs a { color: var(--accent); text-decoration: none; }
  .crumbs .sep { margin: 0 6px; }
  .title-icon { position: absolute; left: 88px; top: 58px; }
  .page-title {
    position: absolute; left: 123px; top: 56px;
    font-size: 20.5px; font-weight: 600; color: var(--ink);
  }

  .card {
    position: absolute; left: 88px; top: 161px; width: 1024px; height: 360px;
    background: var(--white); border-radius: 3px;
    box-shadow: 0 1px 3px rgba(0,0,0,0.05);
  }
  .label { position: absolute; font-size: 9.5px; color: var(--label); }
  .field {
    position: absolute; border: 1px solid var(--line); border-radius: 3px;
    font-size: 11.5px; color: var(--ink); padding-left: 13px;
    display: flex; align-items: center;
  }
  .field .caret { position: absolute; right: 12px; top: 11px; }
  .textarea { align-items: flex-start; padding-top: 11px; color: var(--placeholder); }
  .dropzone {
    position: absolute; left: 28px; top: 161px; width: 450px; height: 171px;
    border: 1.5px dashed var(--dash); border-radius: 3px; background: var(--drop);
    text-align: center;
  }
  .drop-icon {
    width: 48px; height: 48px; border-radius: 50%; background: var(--icon-bg);
    margin: 37px auto 0; display: flex; align-items: center; justify-content: center;
  }
  .drop-text { margin-top: 17px; font-size: 11.5px; line-height: 16px; color: var(--muted); }
  .drop-text a { color: var(--accent); font-weight: 600; text-decoration: none; }

  .divider { position: absolute; left: 88px; top: 549px; width: 1024px; height: 1px; background: var(--line); }
  .btn {
    position: absolute; top: 577px; height: 31px; border-radius: 3px;
    font-size: 11.5px; font-weight: 500; display: flex; align-items: center; justify-content: center;
  }
  .btn-secondary { left: 88px; width: 65px; border: 1px solid var(--accent); color: var(--accent); background: var(--white); }
  .btn-primary { left: 989px; width: 123px; background: var(--accent); color: var(--white); }
</style>
</head>
<body>
  <header class="topbar">
    <div class="brand"><span class="brand-dot"></span>Assessly</div>
    <span class="nav" style="left:752px">Assessments</span>
    <span class="nav active" style="left:849px">Endorsement</span>
    <span class="nav" style="left:948px">Submissions</span>
    <span class="nav" style="left:1040px">Results</span>
    <div class="avatar" role="img" aria-label="User profile photo"></div>
    <svg class="avatar-caret" width="10" height="7" viewBox="0 0 10 7"><path d="M1 1.5l4 4 4-4" fill="none" stroke="#fff" stroke-width="1.6"/></svg>
  </header>

  <section class="page-head">
    <svg class="back" width="19" height="19" viewBox="0 0 20 20"><circle cx="10" cy="10" r="8.8" fill="none" stroke="#0e78bb" stroke-width="1.6"/><path d="M14.5 10H6M9.5 6.3L5.8 10l3.7 3.7" fill="none" stroke="#0e78bb" stroke-width="1.6" stroke-linecap="round" stroke-linejoin="round"/></svg>
    <nav class="crumbs"><a href="#">Submissions</a><span class="sep">/</span>Upload Documents</nav>
    <svg class="title-icon" width="22" height="22" viewBox="0 0 22 22"><path d="M11 13V3M7 6.5L11 2.5l4 4" fill="none" stroke="#4a4f55" stroke-width="1.6" stroke-linecap="round" stroke-linejoin="round"/><path d="M2 12v5a3 3 0 0 0 3 3h12a3 3 0 0 0 3-3v-5h-5a4 4 0 0 1-8 0H2z" fill="none" stroke="#4a4f55" stroke-width="1.6" stroke-linejoin="round"/></svg>
    <h1 class="page-title">Upload Docuements</h1>
  </section>

  <main class="card">
    <span class="label" style="left:28px;top:34px">Document Name</span>
    <div class="field" style="left:28px;top:46px;width:450px;height:31px">MyPortfolio_2</div>
    <span class="label" style="left:28px;top:97px">Document Category</span>
    <div class="field" style="left:28px;top:110px;width:450px;height:31px">Resume
      <svg class="caret" width="10" height="7" viewBox="0 0 10 7"><path d="M1 1.5l4 4 4-4" fill="none" stroke="#4a4f55" stroke-width="1.4"/></svg>
    </div>
    <div class="dropzone">
      <div class="drop-icon">
        <svg width="24" height="24" viewBox="0 0 22 22"><path d="M11 13V3M7 6.5L11 2.5l4 4" fill="none" stroke="#8e9398" stroke-width="1.7" stroke-linecap="round" stroke-linejoin="round"/><path d="M2 12v5a3 3 0 0 0 3 3h12a3 3 0 0 0 3-3v-5h-5a4 4 0 0 1-8 0H2z" fill="none" stroke="#8e9398" stroke-width="1.7" stroke-linejoin="round"/></svg>
      </div>
      <p class="drop-text">Drag &amp; Drop here for upload<br>or <a href="#">browse</a> file</p>
    </div>
    <span class="label" style="left:546px;top:34px">Note</span>
    <div class="field textarea" style="left:546px;top:46px;width:450px;height:287px">Write here</div>
  </main>

  <div class="divider"></div>
  <a class="btn btn-secondary">Cancel</a>
  <a class="btn btn-primary">Submit Document</a>
</body>
</html>
```